Storefront signage for Physio clinic

We need a design for our storefront windows at our physiotherapy & Pilates clinic.

The design should be modern and include our logo, website url and services (physiotherapy, pilates, massage).

Some inspirational exercise/pilates/recovery quotes may be included and I would like to see the use of sport/pilates/injury related stock images. I have attached a few examples of what we want (images numbered 1-5). And I have attached our current design and photo of the outside of our clinic.

In the attached images there is also a pdf with measurments of our window panels. We require signage for the areas marked 1-10. As you can see on our current signage, you don't need to have a separate image for each panel, these can flow onto each other.
Updates

Industry/Entity Type

Clinic

Colors
85acd3
3377b5
3277b5
e8e8e8
c3c3c3
9d9d9d
848484
7f7f7f

Requirements
Must have
• Stock images related to sports, physiotherapy and pilates
• Ideally these images should be in greyscale and blend in with the rest of the panel which should include colours.
• I would like to see for example a runner, a weightlifter, someone doing pilates, someone with back pain (not necessarily all of these).
Should not have
• I want a creative, modern, up market design, not just a standard recycled template.

```html
<!DOCTYPE html>
<html lang="en">
<head>
<meta charset="utf-8">
<title>Harbourline Physio – Storefront Window Panels</title>
<link rel="stylesheet" href="https://fonts.googleapis.com/css2?family=Roboto+Condensed:wght@700&family=Roboto:wght@400;500&display=swap">
<style>
  :root{
    --backdrop:#e8e8e8;
    --panel-blue:#1e4ea5;
    --panel-blue-deep:#1a3f88;
    --tag-light:#3aa0dc;
    --tag-dark:#17306b;
    --white:#ffffff;
    --glass-top:#c3c3c3;
    --glass-bottom:#9d9d9d;
    --ring:#85acd3;
    --photo-light:#c3c3c3;
    --photo-mid:#9d9d9d;
    --photo-dark:#7f7f7f;
  }
  *{box-sizing:border-box;margin:0;padding:0}
  html,body{width:1200px;height:714px;overflow:hidden}
  body{background:var(--backdrop);font-family:"Roboto",Arial,sans-serif;position:relative}

  .panel{position:absolute;top:50px;height:614px;overflow:hidden}
  .strip{position:absolute;top:0;height:100%}
  .photo{background:linear-gradient(160deg,var(--photo-light),var(--photo-mid) 55%,var(--photo-dark))}
  .photo.warm{background:linear-gradient(200deg,#d9d9d9,#9d9d9d 50%,#848484)}
  .blue{background:var(--panel-blue)}

  .tag{position:absolute;display:flex;flex-direction:column;align-items:flex-start;gap:2px;
       font-family:"Roboto Condensed",Arial,sans-serif;font-weight:700;text-transform:uppercase;color:var(--white);white-space:nowrap}
  .tag span{display:block;padding:2px 5px;line-height:1.05}
  .tag .top{background:var(--tag-light)}
  .tag .bottom{background:var(--tag-dark)}

  .service-list{position:absolute;top:255px;left:0;width:100%;text-align:center;
       color:var(--white);font-size:6px;line-height:1.7;text-transform:uppercase;white-space:nowrap}

  .brand-name{font-family:"Roboto",Arial,sans-serif;font-weight:500;color:var(--white);text-align:center}
  .brand-mark{display:inline-block;border-radius:50%;background:var(--white)}

  .dots{position:absolute;left:50%;transform:translateX(-50%);display:flex;flex-direction:column;align-items:center}
  .dots i{display:block;width:7px;height:7px;border-radius:50%;background:var(--white)}

  .contact{position:absolute;left:0;width:100%;text-align:center;color:var(--white)}

  .group-a{left:30px;width:180px}
  .group-b{left:230px;width:330px}
  .group-b .feature-name{position:absolute;top:225px;left:0;width:100%;color:var(--panel-blue-deep);
       font-family:"Roboto Condensed",Arial,sans-serif;font-weight:700;font-size:24px;line-height:1.05;text-align:center;text-transform:uppercase}
  .group-b .frame-box{position:absolute;left:110px;top:470px;width:22px;height:54px;border:1.5px solid var(--panel-blue-deep)}
  .group-b .url{position:absolute;bottom:22px;left:0;width:100%;text-align:center;color:var(--white);font-size:9px}

  .door-panel{left:580px;width:150px}
  .glass-door{left:750px;width:230px;background:linear-gradient(180deg,var(--glass-top),var(--glass-bottom))}
  .glass-door .ring{position:absolute;left:15px;top:207px;width:200px;height:200px;border-radius:50%;
       border:3px solid var(--ring);display:flex;align-items:center;justify-content:center}
  .side-panel{left:1000px;width:170px}
</style>
</head>
<body>

  <section class="panel group-a">
    <div class="strip photo" style="left:0;width:44px" role="img" aria-label="Greyscale photo of a runner stretching"></div>
    <div class="strip blue" style="left:44px;width:42px">
      <p class="service-list">Physio<br>•<br>Pilates</p>
    </div>
    <div class="strip photo warm" style="left:86px;width:52px" role="img" aria-label="Greyscale photo of a woman lifting a kettlebell"></div>
    <div class="strip blue" style="left:138px;width:42px">
      <p class="service-list">Massage<br>•<br>Rehab</p>
    </div>
    <div class="tag" style="left:4px;top:205px;font-size:9px"><span class="top">Run</span><span class="bottom">Natural</span></div>
    <div class="tag" style="left:90px;top:205px;font-size:9px"><span class="top">Focus</span><span class="bottom">Achieve</span></div>
  </section>

  <section class="panel group-b">
    <div class="strip photo" style="left:0;width:70px" role="img" aria-label="Greyscale photo of a woman holding a Pilates balance pose"></div>
    <div class="strip blue" style="left:70px;width:160px">
      <p class="feature-name">Harbourline<br>Physio</p>
      <div class="frame-box"></div>
      <p class="url">www.harbourlinephysio.com.au</p>
    </div>
    <div class="strip photo warm" style="left:230px;width:100px" role="img" aria-label="Greyscale photo of a man holding a sore shoulder, highlighted in red"></div>
    <div class="tag" style="left:14px;top:320px;font-size:14px"><span class="top">Better</span><span class="bottom">Balance</span></div>
    <div class="tag" style="left:262px;top:320px;font-size:15px"><span class="top">Pain</span><span class="bottom">Rehab</span></div>
  </section>

  <section class="panel door-panel blue">
    <div class="dots" style="top:110px;gap:36px"><i></i><i></i><i></i></div>
    <div style="position:absolute;top:268px;left:0;width:100%;text-align:center">
      <span class="brand-mark" style="width:10px;height:10px;vertical-align:middle"></span>
      <p class="brand-name" style="font-size:12px;margin-top:6px">Harbourline Physio</p>
    </div>
    <div class="dots" style="top:370px;gap:34px"><i></i><i></i><i></i></div>
    <p class="contact" style="bottom:50px;font-size:11px">02 9000 4182</p>
  </section>

  <section class="panel glass-door">
    <div class="ring">
      <p class="brand-name" style="font-size:22px;line-height:1.15">Harbourline<br>Physio</p>
    </div>
  </section>

  <section class="panel side-panel blue">
    <div class="dots" style="top:110px;gap:48px"><i></i><i></i><i></i></div>
    <div style="position:absolute;top:290px;left:0;width:100%;text-align:center">
      <span class="brand-mark" style="width:12px;height:12px;vertical-align:middle"></span>
      <p class="brand-name" style="font-size:14px;margin-top:6px">Harbourline Physio</p>
    </div>
    <div class="dots" style="top:400px;gap:48px"><i></i><i></i><i></i></div>
    <address class="contact" style="bottom:30px;font-style:normal;font-size:12px;line-height:1.5">
      14 Kestrel Lane<br>Marlow Bay<br><span style="font-size:10px">www.harbourlinephysio.com.au</span>
    </address>
  </section>

</body>
</html>
```